Business card for Eyelash extension salon in Marisol Hills,California USA

We need new business card for our salon in Marisol Hills. The salon name is 'Lashvera' . We would like to have...Business name: Lashvera Name of person: will provide later Address 4720 N.Alder Crest Ave Marisol Hills , CA 90299 Phone: will provide later (Text only) Web: www.lashverastudio.example Snapgrid icon, Circlebook icon follow us for seasonal campaign and news @lashverastudiolounge Design should look elegant, high-end, clean, simple, cohesive with my brand. Please refer my brand board. Business name color will be metallic bronzy color. Im thinking grey background or white background. Thanks

Target Market(s)

25-35. Gender neutral. People who are in Entertainment business industry.
This is High-end Eyelash extension salon in Marisol Hills

Industry/Entity Type

Beauty Salon

Contact Information for Business Card

Business name: Lashvera
Name of person: will provide later
Address 4720 N.Alder Crest Ave Marisol Hills , CA 90299
Phone: will provide later (Text only)
Web: www.lashverastudio.example
Snapgrid icon, Circlebook icon
follow us for seasonal campaign and news @lashverastudiolounge

Requirements
Must have
• Beautiful, elegant, clean and simple look but very attractive and modern
Should not have
• We don't like too clutter, too busy designs.

```html
<!DOCTYPE html>
<html lang="en">
<head>
<meta charset="utf-8">
<title>Lashvera Business Card</title>
<link rel="stylesheet" href="https://fonts.googleapis.com/css2?family=Playfair+Display:wght@400;700&display=swap">
<style>
  :root {
    --bg: #e9e6e2;
    --card-dark: #2a2929;
    --card-light: #ffffff;
    --bronze: #8a6244;
    --ink: #3c3a38;
    --ink-soft: #5a5754;
    --on-dark: #f3f0ec;
  }
  * { margin: 0; padding: 0; box-sizing: border-box; }
  html, body { width: 1200px; height: 912px; overflow: hidden; }
  body {
    background: var(--bg);
    font-family: "Playfair Display", Georgia, serif;
    position: relative;
  }
  .card {
    position: absolute;
    width: 620px;
    height: 354px;
    box-shadow: 0 10px 28px rgba(0,0,0,0.18);
  }
  .card--back { left: 60px; top: 70px; background: var(--card-dark); color: var(--on-dark); }
  .card--front { left: 520px; top: 488px; background: var(--card-light); color: var(--ink); }

  .brand-name {
    font-weight: 400;
    color: var(--bronze);
    letter-spacing: 1px;
    line-height: 1;
    white-space: nowrap;
  }
  .card--back .brand-name {
    position: absolute; left: 0; right: 0; top: 104px;
    text-align: center; font-size: 58px;
  }
  .social {
    position: absolute; left: 0; right: 0; top: 218px;
    display: flex; justify-content: center; gap: 22px;
    font-size: 12px; letter-spacing: 0.5px;
  }
  .social__item { display: flex; align-items: center; gap: 6px; }
  .social__mark { width: 11px; height: 11px; background: var(--on-dark); border-radius: 2px; }
  .follow {
    position: absolute; left: 0; right: 0; top: 262px;
    text-align: center; font-size: 15px;
  }

  .card--front .brand-name {
    position: absolute; right: 60px; top: 62px; font-size: 50px;
  }
  .address {
    position: absolute; right: 40px; top: 196px;
    text-align: right; font-size: 13px; line-height: 1.55; color: var(--ink);
  }
  .person { position: absolute; left: 40px; top: 170px; }
  .person__name {
    font-weight: 700; font-size: 24px; color: var(--bronze); letter-spacing: 0.5px;
  }
  .person__role { font-size: 14px; color: var(--ink-soft); margin-top: 2px; }
  .contact { position: absolute; left: 40px; top: 254px; list-style: none; }
  .contact__item {
    display: flex; align-items: center; gap: 12px;
    font-size: 14px; color: var(--ink); height: 26px;
  }
  .contact__icon { width: 14px; height: 14px; fill: var(--bronze); }
  .accent { color: var(--bronze); }
</style>
</head>
<body>
  <section class="card card--back" aria-label="Card back">
    <div class="brand-name">Lashvera</div>
    <div class="social">
      <span class="social__item"><span class="social__mark"></span>Circlebook</span>
      <span class="social__item"><span class="social__mark"></span>Snapgrid</span>
    </div>
    <p class="follow">Follow us for seasonal campaign and news @lashverastudiolounge</p>
  </section>

  <section class="card card--front" aria-label="Card front">
    <div class="brand-name">Lashvera</div>
    <p class="address">4720 N.Alder Crest Ave Marisol Hills<br>CA 90299</p>
    <div class="person">
      <div class="person__name">MIRA CASTELL</div>
      <div class="person__role">Manager</div>
    </div>
    <ul class="contact">
      <li class="contact__item">
        <svg class="contact__icon" viewBox="0 0 24 24"><path d="M6.6 10.8a15 15 0 0 0 6.6 6.6l2.2-2.2a1 1 0 0 1 1-.25 11.4 11.4 0 0 0 3.6.57 1 1 0 0 1 1 1V20a1 1 0 0 1-1 1A17 17 0 0 1 3 4a1 1 0 0 1 1-1h3.5a1 1 0 0 1 1 1c0 1.25.2 2.45.57 3.6a1 1 0 0 1-.25 1z"/></svg>
        310-555-0148
      </li>
      <li class="contact__item">
        <svg class="contact__icon" viewBox="0 0 24 24"><path d="M2 5h20v14H2z M3.5 6.5 12 13l8.5-6.5z" fill-rule="evenodd"/></svg>
        info@lashverastudio.example
      </li>
      <li class="contact__item">
        <svg class="contact__icon" viewBox="0 0 24 24"><circle cx="12" cy="12" r="10"/><path d="M2 12h20M12 2c3 3 3 17 0 20M12 2c-3 3-3 17 0 20" stroke="#fff" stroke-width="1.4" fill="none"/></svg>
        <span>www.<span class="accent">lashverastudio</span>.example</span>
      </li>
    </ul>
  </section>
</body>
</html>
```